Bright Harbor, LLC Business Card Design

We need a product business card designed for a new company Bright Harbor, LLC. We make and resell waterless RV cleaner, polish and protectant. It cleans and protects in a simple spray and wipe step leaving the surface protected and conditioned to repel dust, dirt, water, smudges, bugs and fingerprints while preventing fogging. Safe on acrylic, plexiglas, lexan, plastic, rubber, painted surfaces, chrome, stainless, aluminum, vinyl, leather, glass.... This is an eco-friendly green product.

We want to play off the company name to tell the consumer that the product is easy to use and associate to the nostalgics 1950's in the USA... Thinking old travel trailer with hot rod truck pulling it as the graphic, maybe the husband cleaning the truck and the wife cleaning the trailer for a Bright Harbor surface.
Updates

Just posted our newly finished logo. Need to have "Cleaner and Protectant" added to the design as well. Thanks everyone that has submitted thus far, i am working to get comments on all.

If you need a different file format, please let me know. Thank you.

Most important info, is the logo, website and the words "Cleaner" or "Clean" along "Protectant" or "Protect" the remainder is of less importance. Highlight: www.brightharborwash.example Focus is on company brand for Brighter Harbor Cleaner product: However, need a section for the following contact info: Walt Ferris (xxx) xxx-xxxx email address Would like space for QR Code if possible.

Target Market(s)

Adults in the USA between ages of 35-75 that are actively involved in the Recreational Vehicle (RV), travel trailer, and hot rod lifestyle. We are targeting the RV marked of the high end travel, 5th wheel and bus RV market. Along with hot rods, automotive and motorcycle market.

Industry/Entity Type

Travel

Requirements
Must have
• Most important info, is the logo, website and the words "Cleaner" or "Clean" along "Protectant" or "Protect" the remainder is of less importance.

Highlight:
www.brightharborwash.example

Focus is on company brand for Brighter Harbor Cleaner product: However, need a section for the following contact info:

Walt Ferris
(xxx) xxx-xxxx
email address
Nice to have
• Would like a space for a QR Code.

```html
<!DOCTYPE html>
<html lang="en">
<head>
<meta charset="utf-8">
<title>Bright Harbor, LLC — Business Card</title>
<link rel="stylesheet" href="https://fonts.googleapis.com/css2?family=Oswald:wght@500;600&family=Open+Sans:wght@400;600;700&display=swap">
<style>
  :root {
    --backdrop: #e9e9eb;
    --card-white: #ffffff;
    --blue-deep: #2b4fae;
    --blue-mid: #1f7fd6;
    --blue-light: #0fa4e6;
    --arc-dark: #1c1c1c;
    --arc-grey: #8a8a8a;
    --ink: #222222;
    --ink-soft: #555555;
    --qr-line: #b5b5b5;
  }
  * { box-sizing: border-box; margin: 0; padding: 0; }
  html, body {
    width: 1200px; height: 718px; overflow: hidden;
    background: var(--backdrop);
  }
  .stage {
    width: 1200px; height: 718px;
    display: flex; align-items: center; justify-content: center;
  }
  .card {
    position: relative;
    width: 840px; height: 480px;
    background: var(--card-white);
    overflow: hidden;
    box-shadow: 0 14px 34px rgba(0,0,0,0.14);
  }
  .card-art { position: absolute; inset: 0; }
  .holder {
    position: absolute; left: 56px; bottom: 120px;
    color: #fff;
  }
  .holder-name {
    font-family: "Oswald", sans-serif;
    font-weight: 600; font-size: 34px; letter-spacing: 2px;
    line-height: 1.1;
  }
  .holder-title {
    font-family: "Open Sans", sans-serif;
    font-weight: 400; font-size: 19px; letter-spacing: 0.5px;
    opacity: 0.95; margin-top: 4px;
  }
  .brand-block {
    position: absolute; right: 48px; top: 40px;
    text-align: right;
  }
  .brand {
    font-family: "Oswald", sans-serif;
    font-weight: 600; font-size: 38px; letter-spacing: 1px;
    line-height: 1.1;
    color: var(--ink);
    text-transform: uppercase;
  }
  .product-line {
    font-family: "Oswald", sans-serif;
    font-weight: 500; font-size: 17px; letter-spacing: 3px;
    color: var(--blue-mid);
    text-transform: uppercase;
    margin-top: 4px;
  }
  .contacts {
    position: absolute; right: 48px; top: 150px;
    list-style: none;
    font-family: "Open Sans", sans-serif;
    font-size: 14px; color: var(--ink-soft);
  }
  .contact {
    display: flex; align-items: center; justify-content: flex-end;
    gap: 12px; height: 28px;
  }
  .contact svg { width: 16px; height: 16px; fill: var(--ink); flex: none; }
  .contact-web {
    font-weight: 700; font-size: 16px; color: var(--blue-deep);
    height: 32px;
  }
  .contact-web svg { fill: var(--blue-deep); }
  .qr-space {
    position: absolute; right: 48px; bottom: 36px;
    width: 96px; height: 96px;
    border: 2px dashed var(--qr-line);
  }
</style>
</head>
<body>
<main class="stage">
  <article class="card">
    <svg class="card-art" viewBox="0 0 840 480" aria-hidden="true">
      <defs>
        <linearGradient id="blueField" x1="0" y1="1" x2="1" y2="0">
          <stop offset="0" stop-color="var(--blue-deep)"/>
          <stop offset="0.55" stop-color="var(--blue-mid)"/>
          <stop offset="1" stop-color="var(--blue-light)"/>
        </linearGradient>
        <linearGradient id="arcBand" x1="0" y1="0" x2="0" y2="1">
          <stop offset="0" stop-color="var(--arc-grey)"/>
          <stop offset="0.5" stop-color="var(--arc-dark)"/>
          <stop offset="1" stop-color="var(--arc-grey)"/>
        </linearGradient>
      </defs>
      <rect class="blue-field" width="840" height="480" fill="url(#blueField)"/>
      <path class="arc-band" d="M520 0 Q330 240 540 480 L840 480 L840 0 Z" fill="url(#arcBand)"/>
      <path class="white-field" d="M544 0 Q356 240 562 480 L840 480 L840 0 Z" fill="var(--card-white)"/>
    </svg>

    <div class="holder">
      <p class="holder-name">WALT FERRIS</p>
      <p class="holder-title">Managing Director</p>
    </div>

    <div class="brand-block">
      <h1 class="brand">Bright Harbor</h1>
      <p class="product-line">Cleaner and Protectant</p>
    </div>

    <ul class="contacts">
      <li class="contact">(555) 014 2290
        <svg viewBox="0 0 16 16"><path d="M3 1h3l1 4-2 1a9 9 0 0 0 5 5l1-2 4 1v3a2 2 0 0 1-2 2C7 15 1 9 1 3a2 2 0 0 1 2-2z"/></svg></li>
      <li class="contact">(555) 014 7731
        <svg viewBox="0 0 16 16"><path d="M4 0h8a1 1 0 0 1 1 1v14a1 1 0 0 1-1 1H4a1 1 0 0 1-1-1V1a1 1 0 0 1 1-1zm1 2v10h6V2zm3 11a1 1 0 1 0 0 2 1 1 0 0 0 0-2z"/></svg></li>
      <li class="contact">walt@brightharborwash.example
        <svg viewBox="0 0 16 16"><path d="M1 3h14v10H1zm1 1v.5l6 4 6-4V4z"/></svg></li>
      <li class="contact contact-web">www.brightharborwash.example
        <svg viewBox="0 0 16 16"><circle cx="8" cy="8" r="7"/></svg></li>
      <li class="contact">12 Harbor Lane, Bend, OR
        <svg viewBox="0 0 16 16"><path d="M8 0a5.5 5.5 0 0 1 5.5 5.5C13.5 10 8 16 8 16S2.5 10 2.5 5.5A5.5 5.5 0 0 1 8 0zm0 3.5a2 2 0 1 0 0 4 2 2 0 0 0 0-4z"/></svg></li>
    </ul>

    <div class="qr-space" role="img" aria-label="Space reserved for QR code"></div>
  </article>
</main>
</body>
</html>
```